NZ First of it's kind solutions directory and marketplace for busy Mums needs a business card design

We need a business card design for our new nationwide business in NZ (long term plans to go global). We provide solutions to the everyday challenges that busy Mums face by connecting them with quality communities and suppliers of carefully selected, relevant products and services. We sell direct via our online marketplace. The final design should communicate our values of inclusivity, quality and smart solutions. Colours should incorporate our logo colour palette of #477077 and #6ba8b2. Our website is at https://www.brightnestmums.example

Target Market(s)

busy Mums, Age 28 – 50, female, income over $100K, location main centres NZ primarily but NZ wide. Is likely juggling work or career with a young family. Probably had hobbies which have fallen by the wayside.
-Wants to succeed in her chosen career without compromising on family life
-to successfully juggle her career without feeling like she is compromising her children
- Is time poor, something always has to give and it’s generally her health (she’ll stay up late, get stressed)
- probably ex corporate or professional career. Has discretional income

Industry/Entity Type

Business

Contact Information for Business Card

Lena Forbisher, Founder, BrightNestMums.example (Strapline Tap; Gather; Sorted), 47 Kowhai Terrace, Ellerslie, Auckland 1051, New Zealand. Mob: 021 483 517 Ph: +64 (0)9 571 4860

Font styles to use
Other font styles liked:
• Raleway, and/or Architects Daughter

Colors
00a990
33b8a4
86cfc6
cfeae6

Requirements
Must have
• the above details, streamline. the logo and colours associated with those logos
Should not have
• foil or metallic colours

```html
<!DOCTYPE html>
<html lang="en">
<head>
<meta charset="utf-8">
<title>BrightNestMums business card</title>
<link rel="stylesheet" href="https://fonts.googleapis.com/css2?family=Raleway:wght@400;500;700;800&display=swap">
<style>
  :root {
    --teal-dark: #477077;
    --teal-light: #6ba8b2;
    --front-top: #6aa8b2;
    --front-bottom: #4a727a;
    --ink: #3d3d3d;
    --paper: #ffffff;
    --stage: #2a2a2a;
  }
  * { margin: 0; padding: 0; box-sizing: border-box; }
  html, body { width: 1189px; height: 1200px; overflow: hidden; background: var(--stage); }
  body { position: relative; font-family: "Raleway", Arial, sans-serif; }

  .card {
    position: absolute;
    left: 171px;
    width: 856px;
    height: 488px;
    border-radius: 26px;
    overflow: hidden;
  }
  .card--front {
    top: 67px;
    background: linear-gradient(to bottom, var(--front-top), var(--front-bottom));
    color: var(--paper);
  }
  .card--back { top: 626px; background: var(--paper); color: var(--ink); }

  .front-brand {
    position: absolute;
    top: 196px;
    left: 0; right: 0;
    display: flex;
    justify-content: center;
    align-items: center;
    gap: 20px;
  }
  .brand-dot {
    width: 52px; height: 52px; border-radius: 50%;
    background: var(--paper);
  }
  .brand-name {
    font-weight: 800;
    font-size: 62px;
    letter-spacing: -1px;
    line-height: 1;
  }
  .front-url {
    position: absolute;
    top: 362px;
    left: 0; right: 0;
    text-align: center;
    font-size: 21px;
    letter-spacing: 3px;
  }
  .front-url strong { font-weight: 700; }

  .holder { position: absolute; left: 47px; top: 50px; }
  .holder-name { font-weight: 800; font-size: 27px; letter-spacing: -0.5px; line-height: 1; }
  .holder-name .first { color: var(--teal-dark); }
  .holder-name .last { color: var(--teal-light); }
  .holder-role { font-size: 21px; font-weight: 500; margin-top: 2px; }

  .back-brand {
    position: absolute; right: 47px; top: 50px;
    font-weight: 800; font-size: 50px; letter-spacing: -1px; line-height: 1;
    color: var(--teal-dark);
  }

  .divider {
    position: absolute; left: 47px; right: 47px; top: 359px;
    height: 2px; background: var(--teal-light);
  }

  .contacts { position: absolute; left: 47px; top: 376px; list-style: none; }
  .contacts li {
    display: flex; align-items: center; gap: 8px;
    font-size: 21px; font-weight: 500; height: 27px;
  }
  .contacts svg { width: 24px; height: 24px; flex: none; }

  .address {
    position: absolute; right: 47px; top: 376px;
    text-align: right; font-size: 21px; font-weight: 500;
    font-style: normal; line-height: 27px;
  }
</style>
</head>
<body>
  <section class="card card--front" aria-label="Card front">
    <div class="front-brand">
      <span class="brand-dot"></span>
      <span class="brand-name">BrightNestMums</span>
    </div>
    <p class="front-url">www.<strong>brightnestmums</strong>.example</p>
  </section>

  <section class="card card--back" aria-label="Card back">
    <div class="holder">
      <p class="holder-name"><span class="first">Lena</span> <span class="last">Forbisher</span></p>
      <p class="holder-role">Founder</p>
    </div>
    <p class="back-brand">BrightNestMums</p>
    <div class="divider"></div>

    <ul class="contacts">
      <li>
        <svg viewBox="0 0 24 24" aria-hidden="true"><circle cx="12" cy="12" r="11" fill="none" stroke="#6ba8b2" stroke-width="1.5"/><rect x="8.5" y="6" width="7" height="12" rx="1.2" fill="none" stroke="#6ba8b2" stroke-width="1.5"/></svg>
        021 483 517
      </li>
      <li>
        <svg viewBox="0 0 24 24" aria-hidden="true"><circle cx="12" cy="12" r="11" fill="#6ba8b2"/><path d="M6 10c0-2 3-3 6-3s6 1 6 3l-2 1-1-2h-6l-1 2zM8 12h8l1 5H7z" fill="#fff"/></svg>
        +64 (0)9 571 4860
      </li>
      <li>
        <svg viewBox="0 0 24 24" aria-hidden="true"><circle cx="12" cy="12" r="11" fill="#6ba8b2"/><g fill="none" stroke="#fff" stroke-width="1.1"><circle cx="12" cy="12" r="6.5"/><ellipse cx="12" cy="12" rx="3" ry="6.5"/><path d="M5.5 12h13M6.5 9h11M6.5 15h11"/></g></svg>
        www.brightnestmums.example
      </li>
    </ul>

    <address class="address">
      47 Kowhai Terrace,<br>
      Ellerslie, Auckland 1051<br>
      New Zealand
    </address>
  </section>
</body>
</html>
```